Elegant Business Card for Technology Company

Client is a supplier of innovative industrial communications and automation equipment since 2002. This contest is to gather fresh ideas for a redesign of the existing business card. Client is looking for design that best communicates tagline "Industrial Networking and Computing Specialist".

Design submissions should look modern, clean, elegant and professional. It should not be cluttered. Use white as the primary colour. Orange and black as secondary colour. Refer to jpeg File 1 on the current design.

Fonts used by Client used include Arial Regular, Arial Black, Roboto Regular, Roboto Black and Lato.

The winning design will be sent for offset printing using super white 250gsm artcard paper (open for suggestions).

Target Market(s)

System Engineers, Project Managers, Purchasing Managers from companies providing engineering services for Smart Cities.

Industry/Entity Type

Information Technology

Contact Information for Business Card

Refer to PDF File 3 for Business Card Details. Priority of short contact information would be as follows Name > Job Title > Email > Mobile > Web > Tel > Fax > Business Address >UEN (UEN represents company registration number)

Font styles to use
Sans Serif

Colors
ffffff
f37122
000000
5c5c5c

Requirements
Must have
• Refer to AI File 2 (Company Logo) & PDF File 3 (Information on Namecard)
Should not have
• No QR codes
• No Social Media Icons
• Do not create full Black or Orange colour background

```html
<!DOCTYPE html>
<html lang="en">
<head>
<meta charset="utf-8">
<title>Velrik Business Card</title>
<link rel="stylesheet" href="https://fonts.googleapis.com/css2?family=Lato:wght@400;700;900&display=swap">
<style>
  :root {
    --white: #ffffff;
    --orange: #f37122;
    --black: #000000;
    --grey: #5c5c5c;
    --stage: #e9e7e4;
  }
  * { margin: 0; padding: 0; box-sizing: border-box; }
  html, body { width: 1200px; height: 1023px; overflow: hidden; }
  body {
    background: var(--stage);
    font-family: "Lato", Arial, sans-serif;
    color: var(--black);
    position: relative;
  }
  .card {
    position: absolute;
    top: 357px;
    width: 540px;
    height: 309px;
    background: var(--white);
    border-radius: 16px;
    box-shadow: 0 6px 18px rgba(0,0,0,0.18);
    overflow: hidden;
  }
  .card--front { left: 45px; }
  .card--back { left: 615px; }

  /* brand mark */
  .brand { position: absolute; display: flex; align-items: center; gap: 10px; }
  .brand__dot { width: 34px; height: 34px; border-radius: 50%; background: var(--orange); }
  .brand__name { font-weight: 900; font-size: 42px; letter-spacing: 1px; color: var(--black); line-height: 1; }
  .card--front .brand { top: 40px; right: 70px; }
  .card--back .brand { top: 126px; left: 230px; }
  .card--back .brand__dot { width: 40px; height: 40px; }
  .card--back .brand__name { font-size: 50px; }

  /* front */
  .person { position: absolute; left: 28px; top: 126px; }
  .person__name { color: var(--orange); font-size: 21px; font-weight: 400; line-height: 1.1; }
  .person__title { color: var(--black); font-size: 13px; margin-top: 2px; }
  .rule { position: absolute; left: 180px; right: 26px; top: 150px; height: 1px; background: var(--black); }
  .contacts { position: absolute; left: 28px; top: 196px; display: flex; font-size: 12.5px; line-height: 1.55; }
  .contacts__col { padding-right: 16px; }
  .contacts__sep { width: 2px; height: 44px; background: var(--black); margin: 2px 16px 0 0; }
  .label { color: var(--orange); display: inline-block; width: 22px; }
  .address { font-size: 12px; line-height: 1.5; }
  .address__note { color: var(--grey); font-size: 10.5px; }

  /* back */
  .band-line { position: absolute; top: 0; bottom: 0; width: 1.5px; background: var(--black); }
  .band-line--left { left: 34px; }
  .band-line--right { left: 70px; }
  .band {
    position: absolute; top: 0; bottom: 0; left: 38px; width: 28px;
    background: var(--orange);
    display: flex; align-items: center; justify-content: center;
  }
  .tagline, .uen {
    writing-mode: vertical-rl;
    font-size: 11.5px;
    white-space: nowrap;
  }
  .tagline { color: var(--white); }
  .uen { position: absolute; left: 102px; top: 64px; color: var(--black); font-size: 12px; letter-spacing: 0.3px; }
</style>
</head>
<body>
  <section class="card card--front" aria-label="Business card front">
    <div class="brand">
      <span class="brand__dot"></span>
      <span class="brand__name">VELRIK</span>
    </div>
    <div class="person">
      <p class="person__name">Daniel Hart</p>
      <p class="person__title">Sales Manager</p>
    </div>
    <div class="rule"></div>
    <div class="contacts">
      <div class="contacts__col">
        <p><span class="label">M :</span>+65 9123 4567</p>
        <p><span class="label">P :</span>+65 6210 3390</p>
        <p><span class="label">F :</span>+65 6210 3391</p>
      </div>
      <div class="contacts__sep"></div>
      <div class="contacts__col">
        <p><span class="label">E :</span>sales@velrik.com.sg</p>
        <p><span class="label">W :</span>www.velrik.com.sg</p>
      </div>
      <div class="contacts__sep"></div>
      <div class="contacts__col address">
        <p>18 Kallo Crescent,</p>
        <p>Kallo Techpark #04-12 <span class="address__note">(Lobby B),</span></p>
        <p>Singapore 401122</p>
      </div>
    </div>
  </section>

  <section class="card card--back" aria-label="Business card back">
    <div class="band-line band-line--left"></div>
    <div class="band">
      <span class="tagline">Industrial Networking and Computing Specialist</span>
    </div>
    <div class="band-line band-line--right"></div>
    <span class="uen">UEN NO: 200304417K</span>
    <div class="brand">
      <span class="brand__dot"></span>
      <span class="brand__name">VELRIK</span>
    </div>
  </section>
</body>
</html>
```